Business card for a Exhibition booth fabrication company

Hi. My company would like to change our corporate name card. We are an events and Exhibition stand builder company. We would like our corporate name card to resonate what we do. I need someone to create something unique that relates to the industry that I am in. The graphic designer should be creative to incorporate the elements of my industry and try to blend in well in the design of the card. Our aim is to ensure that we are unique and our card can look different from our competitors.
Updates

Target Market(s)

Marketing and events manager from all companies

Contact Information for Business Card

The business card should have the following details:
Name
Job Title
Email
Website

Colors

Designer to choose colors to be used in the design.

Requirements
Must have
• The card must be look something that is relevant to the service that I am providing. My website is: www.velmora-buildworks.com
• You can see my website to get more information on what service that I am doing
Nice to have
• On the back of my card, I would like to have a globe image with the incorporation of my company logo. This is to indicate that my services can be done in any part of the world.

```html
<!DOCTYPE html>
<html lang="en">
<head>
<meta charset="utf-8">
<title>Velmora Buildworks – Business Card</title>
<link rel="stylesheet" href="https://fonts.googleapis.com/css2?family=Open+Sans:wght@400;600;700&display=swap">
<style>
  :root {
    --backdrop: #e4e1de;
    --card: #ffffff;
    --brand-red: #e8202a;
    --ink: #3a3a3c;
    --ink-soft: #5b5b5e;
    --rule-dark: #2e2e30;
    --globe-light: #f3f3f4;
    --globe-mid: #e7e7e9;
    --globe-edge: #dcdcdf;
  }
  * { margin: 0; padding: 0; box-sizing: border-box; }
  html, body {
    width: 1200px; height: 997px; overflow: hidden;
    background: var(--backdrop);
    font-family: "Open Sans", Arial, sans-serif;
  }
  .stage { position: relative; width: 1200px; height: 997px; }
  .card {
    position: absolute; width: 520px; height: 297px;
    background: var(--card);
    box-shadow: 0 6px 18px rgba(0,0,0,0.12);
    overflow: hidden;
  }
  .card--front { left: 55px; top: 350px; }
  .card--back { left: 625px; top: 350px; }

  /* Brand wordmark */
  .brand { display: flex; align-items: center; gap: 10px; }
  .brand__dot {
    width: 26px; height: 26px; border-radius: 50%;
    background: var(--brand-red); flex: none;
  }
  .brand__name {
    font-weight: 700; color: var(--ink);
    letter-spacing: 2.5px; text-transform: uppercase; white-space: nowrap;
  }
  .card--front .brand { position: absolute; left: 40px; top: 52px; }
  .card--front .brand__name { font-size: 15px; }

  /* Front: person and contacts */
  .person { position: absolute; left: 40px; top: 142px; right: 0; }
  .person__row { display: flex; align-items: center; }
  .person__name {
    color: var(--brand-red); font-weight: 700; font-size: 14px;
    letter-spacing: 0.3px; white-space: nowrap;
  }
  .person__rule {
    flex: 1; height: 1px; background: var(--brand-red);
    margin-left: 8px; margin-top: 10px;
  }
  .person__title { color: var(--ink-soft); font-size: 12px; margin-top: -1px; }

  .contacts {
    position: absolute; left: 40px; top: 188px;
    color: var(--ink); font-size: 12px; line-height: 19px;
  }
  .contacts__line { display: flex; align-items: center; gap: 5px; white-space: nowrap; }
  .contacts__line--gap { margin-left: 12px; }
  .icon { width: 10px; height: 10px; flex: none; }

  .footer-rule {
    position: absolute; left: 0; right: 0; top: 262px;
    height: 1px; background: var(--rule-dark);
  }
  .footer-band {
    position: absolute; left: 0; right: 0; top: 266px;
    height: 9px; background: var(--brand-red);
  }

  /* Back: globe area behind the wordmark */
  .globe {
    position: absolute; left: 110px; top: 20px; width: 340px; height: 340px;
    border-radius: 50%;
    background: radial-gradient(circle at 62% 30%, var(--globe-light) 0%, var(--globe-mid) 58%, var(--globe-edge) 100%);
    box-shadow: inset -10px -14px 30px rgba(0,0,0,0.04);
  }
  .card--back .brand {
    position: absolute; left: 0; right: 0; top: 132px; justify-content: center;
  }
  .card--back .brand__name { font-size: 18px; letter-spacing: 3px; }
</style>
</head>
<body>
<main class="stage">

  <section class="card card--front" aria-label="Business card front">
    <div class="brand">
      <span class="brand__dot"></span>
      <span class="brand__name">Velmora Buildworks</span>
    </div>

    <div class="person">
      <div class="person__row">
        <span class="person__name">DANIEL REYES</span>
        <span class="person__rule"></span>
      </div>
      <div class="person__title">President</div>
    </div>

    <div class="contacts">
      <div class="contacts__line">
        <svg class="icon" viewBox="0 0 10 10"><rect x="2" y="0.5" width="6" height="9" rx="1.2" fill="none" stroke="#e8202a" stroke-width="1.2"/></svg>
        +974 55501234
      </div>
      <div class="contacts__line">
        <svg class="icon" viewBox="0 0 10 10"><rect x="0.5" y="2" width="9" height="6.5" rx="1" fill="#e8202a"/><path d="M1 2.6 L5 5.6 L9 2.6" fill="none" stroke="#fff" stroke-width="0.9"/></svg>
        info@velmora-buildworks.com
        <span class="contacts__line contacts__line--gap">
          <svg class="icon" viewBox="0 0 10 10"><circle cx="5" cy="5" r="4.3" fill="none" stroke="#e8202a" stroke-width="1.1"/><ellipse cx="5" cy="5" rx="1.8" ry="4.3" fill="none" stroke="#e8202a" stroke-width="0.9"/><line x1="0.7" y1="5" x2="9.3" y2="5" stroke="#e8202a" stroke-width="0.9"/></svg>
          www.velmora-buildworks.com
        </span>
      </div>
      <div class="contacts__line">P.O. Box 4120, Al Noor Street, Doha - Qatar</div>
    </div>

    <div class="footer-rule"></div>
    <div class="footer-band"></div>
  </section>

  <section class="card card--back" aria-label="Business card back">
    <div class="globe" role="img" aria-label="Light grey globe with a world map, showing exhibition stands built anywhere in the world"></div>
    <div class="brand">
      <span class="brand__dot"></span>
      <span class="brand__name">Velmora Buildworks</span>
    </div>
  </section>

</main>
</body>
</html>
```